Business Card Design Project - Brazilian Bespoke Furniture Company

Hi everybody!
We are a little (10 employes) brazilian bespoke furniture company called TLVIEGAS MARCENARIA (where TL are initials, VIEGAS last name of my family and MARCENARIA are our area/segment in brazilian portuguese).
Our card must have 2 sides.
I'd to have a "clean white" business card in front. And it's importante to have an style that I can have or not a personal name and contact. For example, I will use the same design of front to put my personal contacts and to put only the company contacts without any name of an employe.
In back, I want to mix three diferent images to cover all (or almost all) back face (been a bedroom, a tv-room and a kitchen - I really need this three pictures and I sent many picture options if you wanna use) but giving impression are all the same picture (like a 180 degrees picture of a house where there is no separation between the different parts of the house). In back must be the slogan that you can write with any font you think is appropriated. SLOGAN: "sob medida para o lar e para o bolso".
Any questions you have, let me know!
Regards,
Otávio Viegas
I apologize all you cause my project enters without brief and informations.
I changed the slogan: the right one isĀ "sob medida para o lar e para o bolso".
Target Market(s)
People between 30 and 45 years old that are buying houses or moving.
Industry/Entity Type
House
Look and feel
Each slider illustrates characteristics of the customer's brand and the style your logo design should communicate.

```html
<!DOCTYPE html>
<html lang="pt-BR">
<head>
<meta charset="utf-8">
<title>TLVIEGAS MARCENARIA – Cartão de visita</title>
<link href="https://fonts.googleapis.com/css2?family=Arimo:wght@400;700&family=Open+Sans:wght@400&display=swap" rel="stylesheet">
<style>
  :root {
    --stage: #2a2a2a;
    --card-white: #ffffff;
    --brand-orange: #e8562a;
    --slogan-red: #d8452a;
    --ink-grey: #555555;
    --icon-grey: #6f6f6f;
    --back-black: #050505;
    --band-grey: #6a6a6a;
    --tile-cream: #f3efe6;
  }
  * { box-sizing: border-box; margin: 0; padding: 0; }
  html, body { width: 1200px; height: 1000px; overflow: hidden; }
  body {
    background: var(--stage);
    font-family: "Arimo", Arial, sans-serif;
    position: relative;
  }
  .card { position: absolute; overflow: hidden; box-shadow: 0 6px 18px rgba(0,0,0,.5); }

  /* front */
  .card-front { width: 545px; height: 340px; background: var(--card-white); top: 90px; }
  .card-front--personal { left: 30px; }
  .card-front--company { left: 620px; }
  .front-texture {
    position: absolute; top: 0; right: 0; width: 300px; height: 100%;
    background: linear-gradient(100deg, rgba(255,255,255,1) 0%, var(--tile-cream) 45%, #ebe6dc 75%, #f6f3ee 100%);
    opacity: .8;
  }
  .brand-mark {
    position: absolute; left: 40px; top: 62px;
    font-size: 46px; font-weight: 400; color: var(--brand-orange); letter-spacing: 2px;
  }
  .brand-name {
    position: absolute; left: 30px; top: 136px;
    font-size: 14px; font-weight: 400; color: var(--brand-orange); letter-spacing: .5px;
  }
  .contact-list { position: absolute; list-style: none; }
  .contact-list li {
    display: flex; align-items: center; gap: 6px;
    font-size: 10px; color: var(--brand-orange); height: 20px;
  }
  .contact-list svg { width: 13px; height: 13px; flex: none; }
  .company-contacts { left: 35px; top: 263px; }
  .personal-block {
    position: absolute; left: 300px; top: 222px; width: 245px; height: 118px;
    background: var(--card-white);
    box-shadow: -6px 0 8px -4px rgba(0,0,0,.25);
    padding: 8px 0 0 8px;
  }
  .person-name { font-size: 18px; font-weight: 700; color: var(--ink-grey); margin-bottom: 4px; }
  .personal-block .contact-list { position: static; }
  .contact-value { margin-left: 2px; }

  /* back */
  .card-back {
    left: 294px; top: 573px; width: 644px; height: 394px; background: var(--back-black);
  }
  .back-mark {
    position: absolute; top: 28px; width: 100%; text-align: center;
    font-size: 26px; color: var(--brand-orange); letter-spacing: 1px;
  }
  .back-name {
    position: absolute; top: 72px; width: 100%; text-align: center;
    font-size: 8px; color: var(--brand-orange);
  }
  .band { position: absolute; left: 0; width: 100%; height: 6px; background: var(--band-grey); }
  .band--top { top: 88px; }
  .band--bottom { top: 304px; }
  .interior-panorama {
    position: absolute; left: 0; top: 98px; width: 100%; height: 201px;
    background: linear-gradient(90deg, #b89a78 0%, #7c8ea6 18%, #e6e1d8 35%, #f0ede6 55%, #d9d4cc 72%, #6a5244 85%, #cfd5d9 100%);
  }
  .slogan {
    position: absolute; top: 330px; width: 100%; text-align: center;
    font-family: "Open Sans", Verdana, sans-serif; font-size: 15px; color: var(--slogan-red); letter-spacing: .5px;
  }
</style>
</head>
<body>

<svg width="0" height="0" style="position:absolute">
  <defs>
    <symbol id="icon-home" viewBox="0 0 14 14"><rect width="14" height="14" rx="3" fill="#6f6f6f"/><path d="M3 7.5 7 3.5l4 4V11H8.5V8.5h-3V11H3z" fill="#fff"/></symbol>
    <symbol id="icon-web" viewBox="0 0 14 14"><rect width="14" height="14" rx="3" fill="#6f6f6f"/><circle cx="7" cy="7" r="3.6" fill="none" stroke="#fff" stroke-width="1.2"/><path d="M3.4 7h7.2M7 3.4v7.2" stroke="#fff" stroke-width="1"/></symbol>
    <symbol id="icon-mail" viewBox="0 0 14 14"><rect width="14" height="14" rx="3" fill="#6f6f6f"/><text x="7" y="10.5" font-size="9" text-anchor="middle" fill="#fff" font-family="Arial, sans-serif">@</text></symbol>
    <symbol id="icon-phone" viewBox="0 0 14 14"><rect width="14" height="14" rx="3" fill="#6f6f6f"/><path d="M3 5.5c0-1.5 8-1.5 8 0v1H9V5.5H5v1H3z M4.5 7h5l1 3.5h-7z" fill="#fff"/></symbol>
    <symbol id="icon-mobile" viewBox="0 0 14 14"><rect width="14" height="14" rx="3" fill="#6f6f6f"/><rect x="4.8" y="2.5" width="4.4" height="9" rx="1" fill="#fff"/><rect x="5.6" y="3.6" width="2.8" height="5.6" fill="#6f6f6f"/></symbol>
  </defs>
</svg>

<section class="card card-front card-front--personal" aria-label="Frente do cartão com contato pessoal">
  <div class="front-texture" role="img" aria-label="Textura suave de painéis de madeira clara"></div>
  <div class="brand-mark">TLMA</div>
  <div class="brand-name">TLVIEGAS MARCENARIA</div>
  <ul class="contact-list company-contacts">
    <li><svg><use href="#icon-home"/></svg>Address:</li>
    <li><svg><use href="#icon-web"/></svg>Website:</li>
  </ul>
  <div class="personal-block">
    <p class="person-name">Person Name</p>
    <ul class="contact-list">
      <li><svg><use href="#icon-mail"/></svg>Email:<span class="contact-value">xxxxxxxxxx@xxxxxxxxx.xxx</span></li>
      <li><svg><use href="#icon-phone"/></svg>Phone:</li>
      <li><svg><use href="#icon-mobile"/></svg>Mobile:</li>
    </ul>
  </div>
</section>

<section class="card card-front card-front--company" aria-label="Frente do cartão somente com contato da empresa">
  <div class="front-texture" role="img" aria-label="Textura suave de painéis de madeira clara"></div>
  <div class="brand-mark">TLMA</div>
  <div class="brand-name">TLVIEGAS MARCENARIA</div>
  <ul class="contact-list company-contacts">
    <li><svg><use href="#icon-home"/></svg>Address:</li>
    <li><svg><use href="#icon-web"/></svg>Website:</li>
  </ul>
</section>

<section class="card card-back" aria-label="Verso do cartão">
  <div class="back-mark">TLMA</div>
  <div class="back-name">TLVIEGAS MARCENARIA</div>
  <div class="band band--top"></div>
  <div class="interior-panorama" role="img" aria-label="Panorama contínuo de quarto, cozinha e sala de TV com móveis sob medida"></div>
  <div class="band band--bottom"></div>
  <p class="slogan">Sob medida para o lar e para o bolso</p>
</section>

</body>
</html>
```